Pediatric Therapy Clinic Brochure

We need a Brochure for a new pediatric therapy clinic. The clinic offers occupational therapy, physical therapy, speech therapy and feeding therapy. We want a brochure for parents, doctors and medical professional. It should have a fun and inviting, but still professional feel. Should be kid focused, bright and colorful. All the text / wording is there and a rough layout. Now I need someone to tidy and jazz it up and make it look professional.

Target Market(s)

Parents, doctors, medical professional

Industry/Entity Type

Medical

Font styles to use
Serif
Sans Serif

Requirements
Must have
• Keep All the text with information about services the same. Logo on front. Pictures throughout (use any of the pictures provided) (try and match up with corresponding service) (pictures are labeled). Need to have Map and contact info
• Keep colors consistent with our logo
Nice to have
• Background, special effects. Make it look fancy and professional
Should not have
• Not so busy that is takes away from the text

```html
<!DOCTYPE html>
<html lang="en">
<head>
<meta charset="utf-8">
<title>Cedar Brook Pediatric Therapy – Inside Spread</title>
<link href="https://fonts.googleapis.com/css2?family=Oswald:wght@500;600&family=Arimo:wght@400;700&family=Open+Sans:wght@700&display=swap" rel="stylesheet">
<style>
  :root {
    --stage: #382f2f;
    --stage-title: #c9b7b5;
    --navy: #263f6e;
    --navy-deep: #1f3560;
    --night: #17191c;
    --band-dark: #1c242c;
    --orange: #e08a22;
    --rule-blue: #2d6fb8;
    --bullet: #c6d52c;
    --white: #ffffff;
    --logo-blue: #1f7fc0;
  }
  * { box-sizing: border-box; margin: 0; padding: 0; }
  html, body { width: 1200px; height: 1200px; overflow: hidden; }
  body {
    background: var(--stage);
    font-family: "Arimo", Arial, sans-serif;
    color: var(--white);
    position: relative;
  }
  .stage-title {
    position: absolute; top: 78px; left: 0; width: 1200px;
    text-align: center;
    font-family: "Open Sans", Arial, sans-serif;
    font-weight: 700; font-size: 34px; letter-spacing: 0.5px;
    color: var(--stage-title);
  }
  .brochure {
    position: absolute; left: 40px; top: 190px;
    width: 1120px; height: 866px;
    display: flex;
    box-shadow: 0 20px 40px rgba(0,0,0,0.45);
  }
  .panel { position: relative; width: 373.33px; height: 100%; overflow: hidden; }
  .panel--occupational { background: var(--navy); }
  .panel--speech { background: var(--navy-deep); }
  .panel--feeding { background: var(--night); }

  .section-title {
    font-family: "Oswald", Impact, sans-serif;
    font-weight: 600; font-size: 27px; letter-spacing: -0.3px;
    text-align: center; text-transform: uppercase; line-height: 1.1;
  }
  .section-intro {
    font-size: 12.5px; line-height: 1.35; text-align: center;
    margin: 6px auto 0; width: 86%;
  }
  .section-rule {
    display: block; width: 88%; height: 4px; margin: 10px auto 14px;
    background: var(--rule-blue); border-radius: 2px;
  }
  .service-list {
    list-style: none; padding: 0 26px 0 34px;
    font-weight: 700; font-size: 13.2px; line-height: 1.32; color: var(--bullet);
  }
  .service-list li { position: relative; padding-left: 12px; }
  .service-list li::before {
    content: "•"; position: absolute; left: 0; top: 0; font-size: 11px;
  }

  .photo-frame {
    border: 7px solid var(--orange); border-radius: 22px; overflow: hidden;
    box-shadow: 0 4px 10px rgba(0,0,0,0.35);
  }
  .photo-fill { width: 100%; height: 100%; }

  /* Occupational panel */
  .panel--occupational .photo-frame { margin: 26px 24px 0; height: 200px; }
  .panel--occupational .photo-fill { background: linear-gradient(135deg, #f4efe8, #e9c9b6 55%, #d98a6f); }
  .panel--occupational .section-title { margin-top: 20px; }
  .panel-footer-dark {
    position: absolute; left: 0; bottom: 0; width: 100%; height: 214px;
    background: var(--band-dark); padding: 30px 24px 0;
  }
  .panel-footer-dark .photo-frame { height: 160px; }
  .panel-footer-dark .photo-fill { background: linear-gradient(120deg, #b08a6a, #d9b59a 45%, #8a6a55); }

  /* Speech panel */
  .panel--speech .section-title:first-child { margin-top: 30px; }
  .panel--speech .sensory-title { margin-top: 18px; }
  .panel--speech .section-rule { width: 92%; }
  .brand-band {
    position: absolute; left: 0; bottom: 0; width: 100%; height: 150px;
    background: var(--white);
    display: flex; align-items: center; justify-content: center; gap: 10px;
  }
  .brand-mark { width: 16px; height: 16px; border-radius: 50%; background: var(--orange); flex: none; }
  .brand-name {
    font-family: "Arimo", Arial, sans-serif; font-weight: 700;
    font-size: 22px; line-height: 1.15; color: var(--logo-blue); text-align: center;
  }
  .speech-footer-strip {
    position: absolute; left: 0; bottom: 0; width: 100%; height: 150px;
  }

  /* Feeding panel */
  .panel--feeding .section-title:first-child { margin-top: 30px; }
  .panel--feeding .follow-title { margin-top: 16px; }
  .coming-soon {
    position: absolute; right: 0; bottom: 0; width: 100%; height: 230px;
  }
  .coming-soon svg { position: absolute; inset: 0; }
  .coming-soon-note {
    position: absolute; right: 22px; bottom: 110px; width: 170px;
    font-size: 13px; line-height: 1.3; text-align: center; color: var(--white);
  }
</style>
</head>
<body>
  <h1 class="stage-title">INSIDE DESIGN IDEA</h1>

  <main class="brochure">
    <section class="panel panel--occupational">
      <div class="photo-frame">
        <div class="photo-fill" role="img" aria-label="Photo of a smiling child with paint-covered hands"></div>
      </div>
      <h2 class="section-title">Occupational Therapy</h2>
      <p class="section-intro">Helping children build better self-esteem, confidence and independence in all the things they do.</p>
      <span class="section-rule"></span>
      <ul class="service-list">
        <li>Sensory Processing Disorder</li>
        <li>Balance, Coordination, Strength, and Endurance</li>
        <li>Fine Motor and Handwriting</li>
        <li>Visual- Motor Integration</li>
        <li>Play and Social Skills</li>
        <li>Feeding and Oral Motor Skills</li>
        <li>Self-Care</li>
        <li>Academic and Cognitive Skills</li>
        <li>Behavioral Difficulties</li>
        <li>Developmental Delays</li>
      </ul>
      <div class="panel-footer-dark">
        <div class="photo-frame">
          <div class="photo-fill" role="img" aria-label="Photo of three children whispering and smiling"></div>
        </div>
      </div>
    </section>

    <section class="panel panel--speech">
      <h2 class="section-title">Speech Therapy</h2>
      <p class="section-intro">Helping children speak, communicate and understand language.</p>
      <span class="section-rule"></span>
      <ul class="service-list">
        <li>Expressive and Receptive Language</li>
        <li>Speech and Language Developmental Milestones</li>
        <li>Articulation / Intelligibility</li>
        <li>Speech Fluency</li>
        <li>Pragmatics and Social Skills</li>
        <li>Literacy and Vocabulary</li>
        <li>Apraxia of Speech</li>
        <li>Augmentative and Alternative Communication</li>
        <li>Feeding and Oral Motor</li>
      </ul>
      <h2 class="section-title sensory-title">Sensory Integration</h2>
      <p class="section-intro">Gradually increasing play based activities to improve a child's nervous system. Helping children learn to self-regulate their emotions, behaviors and arousal levels.</p>
      <span class="section-rule"></span>
      <ul class="service-list">
        <li>Autism and ADHD</li>
        <li>Sensory Processing Disorder</li>
        <li>Poor Tolerance of Sensory Stimuli from the Environment</li>
        <li>Meltdowns and Tantrums</li>
        <li>Poor Balance/Body Awareness</li>
        <li>Poor Attention and Concentration</li>
        <li>Poor Self-Regulation</li>
        <li>Behavior and Social Difficulties</li>
        <li>Poor Motor Coordination and Motor Planning</li>
        <li>Aggression, Frustration or Avoidance Behaviors</li>
      </ul>
      <div class="brand-band">
        <span class="brand-mark"></span>
        <p class="brand-name">Cedar Brook<br>Pediatric Therapy</p>
      </div>
    </section>

    <section class="panel panel--feeding">
      <h2 class="section-title">Feeding Therapy</h2>
      <p class="section-intro">Providing skilled assessment and intervention to children with feeding difficulties.</p>
      <span class="section-rule"></span>
      <ul class="service-list">
        <li>Food Aversions</li>
        <li>Food Refusal</li>
        <li>Very Picky Eating</li>
        <li>Avoidance of Certain Textures</li>
        <li>Gagging and Vomiting</li>
        <li>Oral Motor/ Chewing Difficulties</li>
        <li>Limited Diet/Food Repertoire</li>
      </ul>
      <h2 class="section-title follow-title">Physical Therapy</h2>
      <p class="section-intro">Helping children move and interact within their environment smoothly and confidently.</p>
      <span class="section-rule"></span>
      <ul class="service-list">
        <li>Torticollis</li>
        <li>Walking and Mobility</li>
        <li>Developmental Motor Milestones</li>
        <li>Balance, Coordination, Motor Planning</li>
        <li>Strength, Muscle Tone and Range of Motion</li>
        <li>Sports Injuries</li>
        <li>Toe Walking</li>
        <li>Myofascial Release</li>
        <li>Postural Control and Positioning</li>
      </ul>
      <h2 class="section-title follow-title">Group Therapy</h2>
      <p class="section-intro">Using peer role models to learn new and challenging skills.</p>
      <span class="section-rule"></span>
      <ul class="service-list">
        <li>Social Groups</li>
        <li>Feeding Groups</li>
      </ul>
      <div class="coming-soon">
        <svg viewBox="0 0 373 230" preserveAspectRatio="none" aria-hidden="true">
          <path d="M373 0 C300 70 180 150 40 230 L373 230 Z" fill="var(--orange)"/>
          <path d="M373 0 C300 70 180 150 40 230" fill="none" stroke="var(--rule-blue)" stroke-width="4"/>
        </svg>
        <p class="coming-soon-note">**More Group Classes Coming Soon</p>
      </div>
    </section>
  </main>
</body>
</html>
```